Harborview Estates Business Card for Apartment Buildings

Create business cards for resident managers who run apartment buildings. The audience is the public who are searching for apartment rentals, and current residents who live at the apartment building. Key design element will be incorporating the company logo, however, the logo cannot dominate. The building name and manager name are more important than the logo. Current business card design leaves little room for copy, so we may need to reduce the size on the current card to allow for more space for copy.

Target Market(s)

Adults 18-65 years of age, who are looking for an apartment rental, plus current residents who live at our apartment buildings.

Industry/Entity Type

Property Management

Contact Information for Business Card

A major design element will be use of the company logo. Important property and manager contact information must be part of the design. The size of the logo will need to be reduced to make room for building and manager contact copy.

Font styles to use
Sans Serif

Colors
3176b5
000000
959595
ffffff

Requirements
Must have
• 1) Incorporate the company logo.
• 2) Use the company colors (dark blue, black/grey, over white).
• 3) FEATURE THE BUILDING NAME
• 4) FEATURE THE MANAGER NAME
• 5) The company name is less important than BUILDING and MANAGER
• 6) Manager contact information
• **SEE ATTACHED CREATIVE BRIEF**
Nice to have
• 1) Back of card logo watermark
• 2) Ability to write notes on back of carfd
Should not have
• Avoid letting the company logo dominate the card, the building name and manager are more important than the company logo.

```html
<!DOCTYPE html>
<html lang="en">
<head>
<meta charset="utf-8">
<title>Harborview Estates – Resident Manager Business Card</title>
<link rel="stylesheet" href="https://fonts.googleapis.com/css2?family=Catamaran:wght@400;600;700&display=swap">
<style>
  :root {
    --brand-blue: #1b6aa8;
    --ink-grey: #4a4a4a;
    --text-grey: #555555;
    --rule-grey: #8c8c8c;
    --card-white: #ffffff;
    --card-back: #e4e5e6;
    --backdrop: #a3a3a3;
  }
  * { box-sizing: border-box; margin: 0; padding: 0; }
  html, body {
    width: 1200px; height: 1200px; overflow: hidden;
    background: var(--backdrop);
    font-family: "Catamaran", sans-serif;
  }
  .canvas { position: relative; width: 1200px; height: 1200px; }
  .card {
    position: absolute; left: 206px; width: 788px; height: 450px;
  }
  .card--front { top: 94px; background: var(--card-white); }
  .card--back { top: 656px; background: var(--card-back); }

  .building-name {
    position: absolute; left: 40px; top: 44px;
    font-size: 42px; font-weight: 600; color: var(--brand-blue);
    letter-spacing: 0.2px; line-height: 1.1;
  }
  .building-address {
    position: absolute; left: 40px; top: 96px;
    font-size: 19px; line-height: 31px; color: var(--text-grey); font-weight: 400;
  }
  .manager-marker {
    position: absolute; left: 0; top: 166px; width: 10px; height: 32px;
    background: var(--brand-blue);
  }
  .manager-name {
    position: absolute; left: 40px; top: 164px;
    font-size: 27px; font-weight: 700; color: var(--brand-blue); line-height: 1.2;
  }
  .manager-role {
    position: absolute; left: 40px; top: 199px;
    font-size: 19px; color: var(--text-grey); line-height: 1.3;
  }
  .contact-list {
    position: absolute; left: 40px; top: 254px; list-style: none;
  }
  .contact-list li {
    display: flex; align-items: center; height: 31px;
    font-size: 19px; color: var(--text-grey);
  }
  .contact-list svg {
    width: 15px; height: 15px; margin-right: 12px; fill: var(--brand-blue);
  }

  .company-name {
    position: absolute; left: 40px; top: 46px;
    display: flex; align-items: center;
    font-size: 30px; font-weight: 700; color: var(--brand-blue);
  }
  .company-name .dot {
    width: 34px; height: 34px; border-radius: 50%;
    background: var(--ink-grey); margin-right: 12px;
  }
  .note-lines { position: absolute; left: 40px; top: 173px; width: 710px; }
  .note-lines span {
    display: block; height: 42px; border-top: 1px solid var(--rule-grey);
  }
</style>
</head>
<body>
<main class="canvas">
  <section class="card card--front" aria-label="Card front">
    <h1 class="building-name">Cedar Point Apartments</h1>
    <p class="building-address">1482 Linden Avenue San<br>Diego, CA 92116</p>
    <div class="manager-marker"></div>
    <h2 class="manager-name">Marisol Vega</h2>
    <p class="manager-role">Resident Manager</p>
    <ul class="contact-list">
      <li><svg viewBox="0 0 16 16" aria-hidden="true"><path d="M3.5 1l2.6 3-1.4 1.8c.9 2 2.6 3.7 4.6 4.6L11 9l3 2.6-1.3 2.6C7 14 2 9 1.8 3.3z"/></svg>619-555-0142</li>
      <li><svg viewBox="0 0 16 16" aria-hidden="true"><path d="M4 1h8v4H4zM1 6h14v6h-3v3H4v-3H1zm4 4v4h6v-4z"/></svg>619-555-0187</li>
      <li><svg viewBox="0 0 16 16" aria-hidden="true"><path d="M4 0h8a1 1 0 011 1v14a1 1 0 01-1 1H4a1 1 0 01-1-1V1a1 1 0 011-1zm1 2v10h6V2zm3 11a1 1 0 100 2 1 1 0 000-2z"/></svg>619-555-0163</li>
      <li><svg viewBox="0 0 16 16" aria-hidden="true"><path d="M1 3h14v10H1zm1.5 1.3v.4L8 9l5.5-4.3v-.4zm0 2.2V12h11V6.5L8 10.7z"/></svg>marisol@harborviewest.com</li>
      <li><svg viewBox="0 0 16 16" aria-hidden="true"><path d="M8 1a7 7 0 100 14A7 7 0 008 1zm-.7 1.6C6.4 3.7 5.9 5.2 5.8 7.3H2.6a5.5 5.5 0 014.7-4.7zm1.4 0a5.5 5.5 0 014.7 4.7h-3.2c-.1-2.1-.6-3.6-1.5-4.7zM7.3 4v3.3h-.1H7.3zM2.6 8.7h3.2c.1 2.1.6 3.6 1.5 4.7a5.5 5.5 0 01-4.7-4.7zm7.6 0h3.2a5.5 5.5 0 01-4.7 4.7c.9-1.1 1.4-2.6 1.5-4.7zM7.2 7.3c.1-1.8.4-3 .8-3.8.4.8.7 2 .8 3.8zm0 1.4h1.6c-.1 1.8-.4 3-.8 3.8-.4-.8-.7-2-.8-3.8z"/></svg>www.harborviewest.com</li>
    </ul>
  </section>

  <section class="card card--back" aria-label="Card back with note lines">
    <div class="company-name"><span class="dot"></span>Harborview Estates</div>
    <div class="note-lines">
      <span></span><span></span><span></span><span></span><span></span><span></span>
    </div>
  </section>
</main>
</body>
</html>
```